New Email Marketing Design Project

I’d like you to make an email template. I’ll be welcoming and on boarding customers via email. And I’d like the branding to stand out. Keep it professional and simple. But be creative.

Design should look amazing on desktop and mobile phones.

Negative white space is ok.

Use stock images

I’ll like to have a spot for a picture of myself so make sure to include a circle where I can show my face so that email viewers will know who is speaking to them.

Target Market(s)

Practice managers, doctors, medical providers

Font styles to use
Sans Serif

Requirements
Must have
• Our Logo, CTA buttons, Same colors as website.
https://www.tarvoclaimservices.com

```html
<!DOCTYPE html>
<html lang="en">
<head>
<meta charset="utf-8">
<title>Tarvo Claim Services – Welcome Email</title>
<link rel="stylesheet" href="https://fonts.googleapis.com/css2?family=Montserrat:wght@400;500;600;700&family=Roboto:wght@400;500;700&display=swap">
<style>
:root{
  --page-bg:#d6d6d6;
  --paper:#ffffff;
  --brand:#2d7aa0;
  --brand-dark:#2b6f93;
  --tile-1:#0093c7;
  --tile-2:#2e80b8;
  --tile-3:#2e7399;
  --ink:#1e1e1e;
  --body:#555555;
  --band:#333333;
  --footer:#a3a3a3;
}
*{box-sizing:border-box;margin:0;padding:0}
html,body{width:1200px;height:1200px;overflow:hidden;background:var(--page-bg)}
.stage{position:relative;width:1200px;height:1200px}
.email{position:absolute;left:201px;top:0;width:887px;height:1335px;background:var(--paper);
  transform:scale(0.8989);transform-origin:top left;overflow:hidden;font-family:'Montserrat',sans-serif}
.header{position:absolute;left:0;top:0;width:887px;height:75px}
.brand{position:absolute;left:20px;top:20px;display:flex;align-items:center;gap:30px}
.brand-dot{width:34px;height:34px;border-radius:50%;border:3px solid var(--brand)}
.brand-name{font-weight:700;font-size:20px;color:var(--brand)}
.helpline{position:absolute;left:505px;top:18px;display:flex;gap:10px;font-family:'Roboto',sans-serif}
.helpline small{display:block;font-size:11px;color:var(--ink)}
.helpline strong{display:block;font-size:15px;font-weight:700;color:var(--ink);margin-top:4px;letter-spacing:.5px}
.cta{position:absolute;left:732px;top:16px;width:139px;height:37px;background:var(--brand);color:#fff;
  font-family:'Roboto',sans-serif;font-weight:500;font-size:13.5px;display:flex;align-items:center;justify-content:center;gap:6px}
.hero{position:absolute;left:0;top:75px}
.title-band{position:absolute;left:0;top:580px;width:571px;height:107px;background:var(--band);
  color:#fff;font-weight:700;font-size:70px;line-height:107px;padding-left:60px}
.title-sub{position:absolute;left:60px;top:680px;font-weight:400;font-size:70px;color:var(--brand);letter-spacing:.5px}
.section{position:absolute;left:60px;width:790px}
.section h2{font-size:12px;font-weight:700;color:var(--ink);margin-bottom:6px}
.section p{font-size:12px;font-weight:600;color:var(--body);line-height:22px}
.about{top:770px}
.more{position:absolute;left:63px;top:886px;width:69px;height:23px;border:1px solid var(--brand);border-radius:2px;
  font-size:7.5px;font-weight:600;color:var(--brand);display:flex;align-items:center;justify-content:center}
.tiles{position:absolute;left:60px;top:926px;width:787px;height:145px;display:flex}
.tile{flex:1;display:flex;flex-direction:column;align-items:center;padding-top:28px;color:#fff;
  font-family:'Roboto',sans-serif;font-size:9.5px;line-height:12px}
.tile p{margin-top:18px;width:132px}
.tile:nth-child(1){background:var(--tile-1)}
.tile:nth-child(2){background:var(--tile-2)}
.tile:nth-child(3){background:var(--tile-3)}
.remote{top:1083px}
.contacts{position:absolute;left:56px;top:1205px;display:flex;align-items:center;gap:18px;
  font-size:8.5px;font-weight:600;color:var(--ink)}
.contact{display:flex;align-items:center;gap:8px}
.footer{position:absolute;left:0;top:1263px;width:887px;height:72px;background:var(--footer)}
.socials{position:absolute;left:667px;top:18px;display:flex;gap:10px}
.socials span{width:35px;height:35px;border-radius:50%;border:2px solid #444}
</style>
</head>
<body>
<div class="stage">
  <div class="email">
    <header class="header">
      <div class="brand"><span class="brand-dot"></span><span class="brand-name">Tarvo Claim Services</span></div>
      <div class="helpline">
        <svg width="20" height="34" viewBox="0 0 20 34"><rect x="2" y="1" width="16" height="32" rx="3" fill="none" stroke="#1b5a9c" stroke-width="2.5"/><line x1="2" y1="27" x2="18" y2="27" stroke="#1b5a9c" stroke-width="2"/></svg>
        <div><small>Need Help? Call Us Now</small><strong>16125550142</strong></div>
      </div>
      <div class="cta">GET IN TOUCH
        <svg width="12" height="12" viewBox="0 0 12 12"><circle cx="6" cy="6" r="6" fill="#fff"/><path d="M4 3.5 7 6 4 8.5" fill="none" stroke="var(--brand)" stroke-width="1.8"/></svg>
      </div>
    </header>

    <svg class="hero" width="887" height="510" viewBox="0 0 887 510">
      <defs>
        <linearGradient id="deskTones" x1="0" y1="0.1" x2="0.85" y2="1">
          <stop offset="0" stop-color="#6f9cc9"/>
          <stop offset="0.2" stop-color="#a9c3de"/>
          <stop offset="0.38" stop-color="#eef1f4"/>
          <stop offset="0.58" stop-color="#f6f6f5"/>
          <stop offset="0.74" stop-color="#c9ccd1"/>
          <stop offset="0.88" stop-color="#5d6169"/>
          <stop offset="1" stop-color="#2f3238"/>
        </linearGradient>
        <linearGradient id="doctorTones" x1="0.3" y1="0" x2="0.6" y2="1">
          <stop offset="0" stop-color="#c9d4de"/>
          <stop offset="0.35" stop-color="#e4e9ee"/>
          <stop offset="0.6" stop-color="#f5f7f9"/>
          <stop offset="0.82" stop-color="#dfe5eb"/>
          <stop offset="1" stop-color="#9fb2c4"/>
        </linearGradient>
        <radialGradient id="heroShade" cx="0.5" cy="0.5" r="0.5">
          <stop offset="0.9" stop-color="#000" stop-opacity="0.18"/>
          <stop offset="1" stop-color="#000" stop-opacity="0"/>
        </radialGradient>
      </defs>
      <circle cx="230" cy="125" r="385" fill="var(--brand-dark)"/>
      <circle cx="195" cy="140" r="362" fill="#fff"/>
      <circle cx="196" cy="150" r="362" fill="url(#heroShade)"/>
      <circle cx="190" cy="145" r="352" fill="url(#deskTones)" role="img" aria-label="Stock photo of hands writing in a notebook beside a laptop on a white desk"/>
      <circle cx="658" cy="343" r="164" fill="url(#heroShade)"/>
      <circle cx="652" cy="335" r="152" fill="url(#doctorTones)" stroke="var(--brand-dark)" stroke-width="12" role="img" aria-label="Portrait photo of the practice owner in a white coat"/>
    </svg>

    <div class="title-band">Tarvo Claim</div>
    <div class="title-sub">Services</div>

    <section class="section about">
      <h2>ABOUT US</h2>
      <p>At Tarvo Claim Services we are focused on providing medical billing services with the highest levels of customer satisfaction &amp; we will do everything we can to meet your expectations. With a variety of offerings to choose from, we’re sure you’ll be happy working with us. Tarvo Claim Services is a company that you can place your trust in. We offer comprehensive and secure billing support</p>
    </section>
    <div class="more">READ MORE ›</div>

    <div class="tiles">
      <div class="tile">
        <svg width="40" height="38" viewBox="0 0 40 38"><circle cx="20" cy="11" r="10" fill="#fff"/><path d="M1 38 Q1 22 20 22 Q39 22 39 38Z" fill="#fff"/></svg>
        <p>Lorem ipsum dolor sit amet, qu ix ei idque intellegat referren</p>
      </div>
      <div class="tile">
        <svg width="40" height="38" viewBox="0 0 40 38"><circle cx="25" cy="14" r="11" fill="none" stroke="#fff" stroke-width="4"/><line x1="17" y1="22" x2="4" y2="35" stroke="#fff" stroke-width="5" stroke-linecap="round"/></svg>
        <p>Lorem ipsum dolor sit amet, qu ix ei idque intellegat referren</p>
      </div>
      <div class="tile">
        <svg width="42" height="38" viewBox="0 0 42 38"><path d="M21 1 41 20H35V38H25V26H17V38H7V20H1Z" fill="#fff"/></svg>
        <p>Lorem ipsum dolor sit amet, qu ix ei idque intellegat referren</p>
      </div>
    </div>

    <section class="section remote">
      <h2>REMOTE MEDICAL BILLING WORK ON THE RISE</h2>
      <p>Remote medical billing work on the rise thanks to COVID-19. Most people are not ready to risk bringing contagion home to their families. Rightfully so, they are choosing to not work at places where there are large crowds or many customers. Preferring smaller less trafficked setting. The trend is only going to continue as new platforms are made available every single week. It has been determined that outsourcing is the way of the future for medical billing. Is your practice on</p>
    </section>

    <div class="contacts">
      <div class="contact">
        <svg width="20" height="28" viewBox="0 0 20 28"><path d="M10 0C4.5 0 0 4.3 0 9.7 0 17 10 28 10 28S20 17 20 9.7C20 4.3 15.5 0 10 0Z" fill="var(--brand)"/><circle cx="10" cy="9.5" r="4" fill="#fff"/></svg>
        <span>210 Cedar Ave Ste 800 Saint<br>Paul, Minnesota 55102</span>
      </div>
      <div class="contact">
        <svg width="16" height="28" viewBox="0 0 16 28"><rect x="1" y="1" width="14" height="26" rx="2" fill="none" stroke="var(--brand)" stroke-width="2"/><line x1="1" y1="22" x2="15" y2="22" stroke="var(--brand)" stroke-width="1.5"/></svg>
        <span>612-555-0142</span>
      </div>
      <div class="contact">
        <svg width="26" height="24" viewBox="0 0 26 24"><rect x="7" y="0" width="12" height="8" fill="var(--brand)"/><rect x="0" y="8" width="26" height="16" rx="2" fill="var(--brand)"/><rect x="14" y="12" width="9" height="9" fill="#fff"/></svg>
        <span>612-555-0143</span>
      </div>
      <div class="contact">
        <svg width="26" height="18" viewBox="0 0 26 18"><rect x="1" y="1" width="24" height="16" fill="none" stroke="var(--brand)" stroke-width="2"/><path d="M1 1 13 11 25 1" fill="none" stroke="var(--brand)" stroke-width="2"/></svg>
        <span>hello@tarvoclaimservices.com</span>
      </div>
    </div>

    <footer class="footer">
      <div class="socials"><span></span><span></span><span></span><span></span></div>
    </footer>
  </div>
</div>
</body>
</html>
```